Maris Dovey Studio Business Cards

Hi - using the information and logo provided I require a two sided business card designed with the following information. The business card is a 'mini card' 3.5" x 1.25".

Front of card should be the logo attached but inverted (so the background is the peach colour and the logo white).

Back should have these details. If we can't fit the Pictogrum and Friendwall part can we just put the little logos.

Tessa Varnold

Art and Design Consultant
Dealer - Curator - Events - Styling - Creative Sourcing

P: 0438 217 604
E: tessa@marisdoveystudio.example
W: www.marisdoveystudio.example
I (pictogram image please): marisdoveystudio F (Friendwall image please): MarisDoveyAdviser

Target Market(s)

Galleries, artists, art buyers, interior design clients, event managers, creative types

Industry/Entity Type

Business

```html
<!DOCTYPE html>
<html lang="en">
<head>
<meta charset="utf-8">
<title>Maris Dovey Studio – Business Cards</title>
<link rel="stylesheet" href="https://fonts.googleapis.com/css2?family=Tinos&family=Josefin+Sans:wght@400&display=swap">
<style>
  :root {
    --backdrop: #6b5a50;
    --front-black: #0c0c0c;
    --front-glow: #3a3a3a;
    --back-grey: #3b3b3d;
    --peach: #f2b79c;
    --white: #ffffff;
    --rule-grey: #555555;
    --muted-grey: #8a8a8a;
    --wordmark-grey: #9a9a9a;
    --band-ink: #3a2f2b;
    --band-rule: #d99f86;
  }
  html, body {
    margin: 0;
    padding: 0;
    width: 1200px;
    height: 960px;
    overflow: hidden;
    background: var(--backdrop);
  }
  .canvas {
    position: relative;
    width: 1200px;
    height: 960px;
  }
  .card {
    position: absolute;
    box-shadow: 0 18px 24px -14px rgba(0,0,0,0.55);
  }
  /* Front */
  .card--front {
    left: 43px;
    top: 58px;
    width: 874px;
    height: 310px;
    background: radial-gradient(ellipse 260px 150px at 445px 80px, var(--front-glow), var(--front-black) 100%);
  }
  .brand-dot {
    position: absolute;
    border-radius: 50%;
    background: var(--peach);
  }
  .card--front .brand-dot {
    left: 393px;
    top: 22px;
    width: 104px;
    height: 104px;
  }
  .wordmark {
    position: absolute;
    margin: 0;
    font-family: "Josefin Sans", sans-serif;
    font-weight: 400;
    letter-spacing: 0.18em;
    text-transform: uppercase;
    color: var(--wordmark-grey);
    white-space: nowrap;
    transform: translateX(-50%);
    line-height: 1;
  }
  .card--front .wordmark {
    left: 445px;
    top: 160px;
    font-size: 26px;
  }
  .rule {
    position: absolute;
    height: 1px;
    background: var(--rule-grey);
  }
  .card--front .rule { left: 94px; width: 697px; }
  .card--front .rule--a { top: 217px; }
  .card--front .rule--b { top: 253px; }
  .card--front .rule--c { top: 292px; }
  .holder {
    position: absolute;
    left: 445px;
    top: 219px;
    margin: 0;
    transform: translateX(-50%);
    font-family: "Tinos", serif;
    font-size: 28px;
    color: var(--white);
    white-space: nowrap;
  }
  .holder__role { font-size: 24px; }
  .services {
    position: absolute;
    left: 445px;
    top: 262px;
    margin: 0;
    transform: translateX(-50%);
    font-family: "Tinos", serif;
    font-size: 18px;
    color: var(--muted-grey);
    white-space: nowrap;
  }
  /* Back */
  .card--back {
    left: 293px;
    top: 462px;
    width: 873px;
    height: 312px;
    background: var(--back-grey);
    overflow: hidden;
  }
  .card--back .rule--top { left: 28px; width: 819px; top: 28px; background: #555557; }
  .card--back .brand-dot {
    left: 136px;
    top: 48px;
    width: 84px;
    height: 84px;
  }
  .card--back .wordmark {
    left: 176px;
    top: 152px;
    font-size: 16px;
  }
  .divider {
    position: absolute;
    left: 326px;
    top: 46px;
    width: 4px;
    height: 160px;
    background: var(--peach);
  }
  .contact {
    position: absolute;
    left: 371px;
    top: 70px;
    margin: 0;
    padding: 0;
    list-style: none;
    font-family: "Tinos", serif;
    font-size: 22px;
    color: var(--white);
  }
  .contact li { height: 41px; white-space: nowrap; }
  .social-band {
    position: absolute;
    left: 0;
    top: 216px;
    width: 873px;
    height: 96px;
    background: var(--peach);
  }
  .social-band .rule { left: 28px; width: 819px; background: var(--band-rule); }
  .social-band .rule--a { top: 17px; }
  .social-band .rule--b { top: 67px; }
  .social {
    position: absolute;
    top: 26px;
    display: flex;
    align-items: center;
    gap: 16px;
    font-family: "Tinos", serif;
    font-size: 24px;
    color: var(--band-ink);
    white-space: nowrap;
  }
  .social--pictogrum { left: 53px; }
  .social--friendwall { left: 523px; }
  .social__mark {
    width: 32px;
    height: 32px;
    background: var(--band-ink);
  }
  .social-sep {
    position: absolute;
    left: 447px;
    top: 32px;
    width: 1px;
    height: 22px;
    background: var(--band-ink);
  }
</style>
</head>
<body>
<main class="canvas">

  <section class="card card--front" aria-label="Business card front">
    <span class="brand-dot" aria-hidden="true"></span>
    <p class="wordmark">Maris Dovey Studio</p>
    <span class="rule rule--a"></span>
    <p class="holder">Tessa Varnold <span class="holder__role">(Art and Design Consultant)</span></p>
    <span class="rule rule--b"></span>
    <p class="services">Dealer | Curator | Events | Styling | Creative Sourcing</p>
    <span class="rule rule--c"></span>
  </section>

  <section class="card card--back" aria-label="Business card back">
    <span class="rule rule--top"></span>
    <span class="brand-dot" aria-hidden="true"></span>
    <p class="wordmark">Maris Dovey Studio</p>
    <span class="divider"></span>
    <ul class="contact">
      <li>Phone: 0438 217 604</li>
      <li>Email: tessa@marisdoveystudio.example</li>
      <li>Web: www.marisdoveystudio.example</li>
    </ul>
    <div class="social-band">
      <span class="rule rule--a"></span>
      <span class="rule rule--b"></span>
      <div class="social social--pictogrum">
        <span class="social__mark" role="img" aria-label="Pictogrum"></span>
        <span>marisdoveystudio</span>
      </div>
      <span class="social-sep"></span>
      <div class="social social--friendwall">
        <span class="social__mark" role="img" aria-label="Friendwall"></span>
        <span>MarisDoveyAdviser</span>
      </div>
    </div>
  </section>

</main>
</body>
</html>
```